Young Up and Coming Contractor Needs a Super Cool Website

I need a progressive, creative, and edgy website for my construction company. I've been in business since 2014 in Madison Wisconsin. I do residential and commercial projects to include new construction, renovation, remodel of kitchen and baths, tile, drywall, and flooring. I want the website to represent what I do or the essence of my company. I need for you to give me a website that says I'm in the business of building, fixing, and remaking bricks and mortar. I would like to see designs that communicate quality craftsmanship from a talented young contractor. The company is The Brisendale Company, The Brisendale Company.

Target Market(s)

Residential and commercial clients in need of remodeling, renovation, and new construction.

Coding

Coded - Design and coding required

Number of Pages Required

4 page

Font styles to use
Sans Serif

Colors

Designer to choose colors to be used in the design.

Requirements
Must have
• I would like the website to have four pages to include Home, About, Projects, Contact. I want the design to reflect a younger more progressive vibe while still portraying a professional image. I'm looking for a clean modern design that appeals to both residential and commercial clientele.
Should not have
• Please don't make it boring.

```html
<!DOCTYPE html>
<html lang="en">
<head>
<meta charset="utf-8">
<title>The Brisendale Company</title>
<link href="https://fonts.googleapis.com/css2?family=Exo+2:wght@500;600;700&family=Arimo:wght@400;700&display=swap" rel="stylesheet">
<style>
:root{
  --green:#7dc13b;
  --green-soft:rgba(125,193,59,.82);
  --ink:#333333;
  --muted:#666666;
  --light:#f4f4f4;
  --white:#ffffff;
  --footer:#262626;
  --footer-line:#3a3a3a;
}
*{margin:0;padding:0;box-sizing:border-box}
html,body{width:1200px;height:2347px;overflow:hidden}
body{position:relative;background:var(--white);font-family:"Arimo",Arial,sans-serif;color:var(--muted)}
.abs{position:absolute}

/* header */
.site-header{left:0;top:0;width:1200px;height:113px;background:var(--white);border-top:4px solid var(--green)}
.brand{left:85px;top:40px;display:flex;align-items:center;gap:12px}
.brand-mark{width:20px;height:20px;background:var(--green);flex:none}
.brand-name{font-family:"Exo 2",sans-serif;font-weight:700;color:var(--green);font-size:22px;line-height:1.1}
.call{right:85px;top:16px;display:flex;align-items:center;gap:12px;font-family:"Exo 2",sans-serif;font-weight:600;color:var(--green);font-size:16px;letter-spacing:.5px}
.call-dot{width:40px;height:40px;border-radius:50%;background:var(--green);display:flex;align-items:center;justify-content:center}
.nav{right:85px;top:74px;display:flex;gap:62px;font-family:"Exo 2",sans-serif;font-weight:600;font-size:13px;color:var(--ink)}
.nav .active{color:var(--green)}

/* hero */
.hero-photo{left:0;top:113px;width:1200px;height:521px;background:linear-gradient(90deg,#d9d6d1 0%,#c9c1b4 30%,#3d4d66 50%,#c89a4a 62%,#3a4a63 75%,#e2c22a 88%,#d8d2c8 100%)}
.hero-card{left:69px;top:285px;width:435px;height:235px;background:var(--green-soft);padding:22px 22px}
.hero-card h1{font-family:"Exo 2",sans-serif;font-weight:700;color:var(--white);font-size:28px;letter-spacing:.3px;white-space:nowrap}
.hero-card p{color:var(--white);font-size:12px;line-height:24px;margin-top:10px}
.btn-outline{display:inline-block;border:1px solid var(--white);color:var(--white);font-family:"Exo 2",sans-serif;font-weight:700;font-size:14px;padding:12px 16px;margin-top:20px}

/* services */
.services{left:0;top:634px;width:1200px;height:696px;background:var(--light)}
.section-title{width:100%;text-align:center;font-family:"Exo 2",sans-serif;font-weight:700;color:var(--green);font-size:26px;letter-spacing:.5px}
.section-sub{width:100%;text-align:center;font-size:12px;color:var(--muted)}
.service{width:300px;text-align:center}
.service svg{display:block;margin:0 auto}
.service h3{font-family:"Exo 2",sans-serif;font-weight:700;color:var(--green);font-size:16px;margin-top:18px}
.service p{font-size:12px;line-height:25px;margin-top:12px}

/* projects */
.project{width:328px}
.project-photo{width:328px;height:202px}
.project h3{font-family:"Exo 2",sans-serif;font-weight:700;color:var(--green);font-size:18px;margin-top:24px}
.project p{font-size:12px;line-height:25px;margin-top:10px}

/* about */
.about{left:0;top:1745px;width:1200px;height:294px;background:var(--green);text-align:center}
.about h2{font-family:"Exo 2",sans-serif;font-weight:700;color:var(--white);font-size:26px;margin-top:50px}
.about p{color:var(--white);font-size:12px;line-height:28px;width:720px;margin:20px auto 0}
.btn-pill{display:inline-block;width:230px;height:49px;line-height:47px;border:1px solid var(--white);border-radius:25px;color:var(--white);font-family:"Exo 2",sans-serif;font-weight:600;font-size:13px;margin-top:34px}

/* footer */
.site-footer{left:0;top:2039px;width:1200px;height:308px;background:var(--footer);color:var(--white)}
.footer-brand{left:106px;top:88px;width:260px;display:flex;align-items:center;gap:14px}
.footer-brand .brand-mark{width:26px;height:26px}
.footer-brand .brand-name{font-size:30px}
.f-col h4{font-family:"Exo 2",sans-serif;font-weight:600;font-size:17px;margin-bottom:24px}
.f-col p,.f-col li{font-size:12px;line-height:20px}
.contact-list{list-style:none}
.contact-list li{display:flex;gap:12px;margin-bottom:10px;align-items:flex-start}
.contact-list svg{flex:none;margin-top:3px}
.contact-list a{color:var(--white);text-decoration:underline}
.email-field{width:208px;height:34px;background:var(--white);color:#888;font-size:12px;padding:10px 14px;margin-top:20px}
.subscribe{display:inline-block;background:var(--green);font-size:10px;font-weight:700;padding:7px 10px;margin-top:10px}
.socials{display:flex;gap:8px;margin-top:22px}
.socials span{width:34px;height:34px;border:2px solid var(--white);border-radius:50%}
.footer-line{left:85px;top:230px;width:1030px;height:1px;background:var(--footer-line)}
.copyright{left:0;top:266px;width:1200px;text-align:center;font-size:12px}
</style>
</head>
<body>

<header class="abs site-header">
  <div class="abs brand">
    <span class="brand-mark"></span>
    <span class="brand-name">THE BRISENDALE COMPANY</span>
  </div>
  <div class="abs call">
    <span class="call-dot"><svg width="18" height="18" viewBox="0 0 24 24"><path fill="#fff" d="M6.6 10.8a15 15 0 0 0 6.6 6.6l2.2-2.2c.3-.3.7-.4 1-.2 1.1.4 2.3.6 3.6.6.6 0 1 .4 1 1V20c0 .6-.4 1-1 1A17 17 0 0 1 3 4c0-.6.4-1 1-1h3.5c.6 0 1 .4 1 1 0 1.3.2 2.5.6 3.6.1.3 0 .7-.2 1z"/></svg></span>
    CALL US : (000)-555-0142
  </div>
  <nav class="abs nav">
    <span class="active">HOME</span><span>ABOUT</span><span>PROJECTS</span><span>CONTACT</span>
  </nav>
</header>

<section>
  <div class="abs hero-photo" role="img" aria-label="Contractor in a plaid shirt with a tool belt, holding a phone and a yellow hard hat"></div>
  <div class="abs hero-card">
    <h1>BRISENDALE REMODELING</h1>
    <p>Sed ut perspiciatis unde omnis iste natus error sit voluptatem accusantium doloremque laudantium, totam rem aperiam, eaque ipsa quae ab illo inve quasi architecto beatae vitae dicta sunt explicabo.</p>
    <span class="btn-outline">READ MORE</span>
  </div>
</section>

<section class="abs services">
  <h2 class="abs section-title" style="top:34px">OUR SERVICES</h2>
  <p class="abs section-sub" style="top:80px">Sed ut perspiciatis unde omnis iste natus error sit voluptatem accusantium doloremque laudantium</p>
</section>

<div class="abs service" style="left:96px;top:770px">
  <svg width="96" height="112" viewBox="0 0 96 112"><circle cx="48" cy="56" r="44" fill="none" stroke="#7dc13b" stroke-width="6"/><rect x="31" y="44" width="34" height="24" rx="3" fill="#333"/></svg>
  <h3>NEW CONSTRUCTION</h3>
  <p>Sed ut perspiciatis unde omnis iste natus error sit voluptatem accusantium doloremque laudantium, beatae vitae dicta sunt explicabo.</p>
</div>
<div class="abs service" style="left:448px;top:770px">
  <svg width="96" height="112" viewBox="0 0 96 112"><circle cx="48" cy="56" r="44" fill="none" stroke="#7dc13b" stroke-width="6"/><path d="M36 44l24 24M60 44 36 68" stroke="#333" stroke-width="6" stroke-linecap="round"/></svg>
  <h3>RENOVATION</h3>
  <p>Sed ut perspiciatis unde omnis iste natus error sit voluptatem accusantium doloremque laudantium, beatae vitae dicta sunt explicabo.</p>
</div>
<div class="abs service" style="left:804px;top:770px">
  <svg width="96" height="112" viewBox="0 0 96 112"><circle cx="48" cy="56" r="44" fill="none" stroke="#7dc13b" stroke-width="6"/><rect x="31" y="52" width="34" height="22" fill="none" stroke="#333" stroke-width="3"/><path d="M31 59h34M48 59v15" stroke="#333" stroke-width="3"/><rect x="41" y="42" width="14" height="6" fill="#333"/></svg>
  <h3>REMODEL OF KITCHEN</h3>
  <p>Sed ut perspiciatis unde omnis iste natus error sit voluptatem accusantium doloremque laudantium, beatae vitae dicta sunt explicabo.</p>
</div>
<div class="abs service" style="left:96px;top:1037px">
  <svg width="96" height="112" viewBox="0 0 96 112"><circle cx="48" cy="56" r="44" fill="none" stroke="#7dc13b" stroke-width="6"/><path d="M48 41 66 56 48 71 30 56z" fill="none" stroke="#333" stroke-width="3"/><path d="M39 48.5l18 15M57 48.5 39 63.5" stroke="#333" stroke-width="2"/></svg>
  <h3>TILE</h3>
  <p>Sed ut perspiciatis unde omnis iste natus error sit voluptatem accusantium doloremque laudantium, beatae vitae dicta sunt explicabo.</p>
</div>
<div class="abs service" style="left:448px;top:1037px">
  <svg width="96" height="112" viewBox="0 0 96 112"><circle cx="48" cy="56" r="44" fill="none" stroke="#7dc13b" stroke-width="6"/><rect x="30" y="43" width="36" height="26" fill="#333"/><path d="M30 49.5h36M30 56h36M30 62.5h36M39 43v6.5M53 43v6.5M46 49.5v6.5M60 49.5v6.5M39 56v6.5M53 56v6.5M46 62.5v6.5" stroke="#fff" stroke-width="1.5"/></svg>
  <h3>DRYWALL</h3>
  <p>Sed ut perspiciatis unde omnis iste natus error sit voluptatem accusantium doloremque laudantium, beatae vitae dicta sunt explicabo.</p>
</div>
<div class="abs service" style="left:804px;top:1037px">
  <svg width="96" height="112" viewBox="0 0 96 112"><circle cx="48" cy="56" r="44" fill="none" stroke="#7dc13b" stroke-width="6"/><rect x="32" y="40" width="32" height="32" fill="none" stroke="#333" stroke-width="3"/><path d="M32 50.7h32M32 61.3h32M42.7 40v32M53.3 40v32M34 70l28-28" stroke="#333" stroke-width="1.5"/></svg>
  <h3>FLOORING</h3>
  <p>Sed ut perspiciatis unde omnis iste natus error sit voluptatem accusantium doloremque laudantium, beatae vitae dicta sunt explicabo.</p>
</div>

<article class="abs project" style="left:85px;top:1371px">
  <div class="project-photo" role="img" aria-label="Worker with a hammer and tool belt in a hardware store aisle" style="background:linear-gradient(90deg,#c9714a,#e2a864 45%,#d9b27a 70%,#e8d9a0)"></div>
  <h3>FIXING</h3>
  <p>Sed ut perspiciatis unde omnis iste natus error sit voluptatem accusantium doloremque laudantium, totam rem aperiam be atae vitae dicta sunt explicabo.</p>
</article>
<article class="abs project" style="left:436px;top:1371px">
  <div class="project-photo" role="img" aria-label="Room under renovation with exposed brick and new drywall" style="background:linear-gradient(90deg,#8a7565,#cfc3b4 40%,#b7a58f 70%,#7c6b5d)"></div>
  <h3>REMAKING BRICKS</h3>
  <p>Sed ut perspiciatis unde omnis iste natus error sit voluptatem accusantium doloremque laudantium, totam rem aperiam be atae vitae dicta sunt explicabo.</p>
</article>
<article class="abs project" style="left:786px;top:1371px">
  <div class="project-photo" role="img" aria-label="Bricklayer spreading mortar on a brick wall with a trowel" style="background:linear-gradient(135deg,#9e3d24,#c8603c 45%,#6e6258 70%,#b9543a)"></div>
  <h3>MORTAR</h3>
  <p>Sed ut perspiciatis unde omnis iste natus error sit voluptatem accusantium doloremque laudantium, totam rem aperiam be atae vitae dicta sunt explicabo.</p>
</article>

<section class="abs about">
  <h2>ABOUT US</h2>
  <p>Sed ut perspiciatis unde omnis iste natus error sit voluptatem accusantium doloremque laudantium, totam rem aperiam, eaque ipsa quae ab illo inventore veritatis et quasi architecto beatae vitae dicta sunt explicabo.Nemo enim ipsam voluptatem quia voluptas sit sed quia consequuntur magni dolores eos qui ratione voluptatem sequi nesciunt.</p>
  <span class="btn-pill">CLICK HERE FOR MORE INFO</span>
</section>

<footer class="abs site-footer">
  <div class="abs footer-brand">
    <span class="brand-mark"></span>
    <span class="brand-name">THE BRISENDALE COMPANY</span>
  </div>

  <div class="abs f-col" style="left:404px;top:44px;width:210px">
    <h4>CONTACT US</h4>
    <ul class="contact-list">
      <li><svg width="12" height="12" viewBox="0 0 24 24"><path fill="#fff" d="M6.6 10.8a15 15 0 0 0 6.6 6.6l2.2-2.2c.3-.3.7-.4 1-.2 1.1.4 2.3.6 3.6.6.6 0 1 .4 1 1V20c0 .6-.4 1-1 1A17 17 0 0 1 3 4c0-.6.4-1 1-1h3.5c.6 0 1 .4 1 1 0 1.3.2 2.5.6 3.6.1.3 0 .7-.2 1z"/></svg>(000)-555-0142 &nbsp;(Phone)</li>
      <li><svg width="12" height="12" viewBox="0 0 24 24"><rect x="5" y="2" width="14" height="7" fill="#fff"/><rect x="2" y="10" width="20" height="9" rx="2" fill="#fff"/><rect x="6" y="16" width="12" height="6" fill="#fff"/></svg>(000)-555-0142 &nbsp;&nbsp;(Fax)</li>
      <li><svg width="12" height="12" viewBox="0 0 24 24"><rect x="2" y="5" width="20" height="14" fill="#fff"/><path d="M2 5l10 8 10-8" fill="none" stroke="#262626" stroke-width="2"/></svg><a>hello@brisendale-build.com</a></li>
      <li><svg width="12" height="12" viewBox="0 0 24 24"><path fill="#fff" d="M12 2a7 7 0 0 0-7 7c0 5 7 13 7 13s7-8 7-13a7 7 0 0 0-7-7zm0 9.5A2.5 2.5 0 1 1 12 6.5a2.5 2.5 0 0 1 0 5z"/></svg><span># 2564 Lorem Ipsum Dummy<br>Lorem Ipsum Dummy</span></li>
    </ul>
  </div>

  <div class="abs f-col" style="left:636px;top:44px;width:220px">
    <h4>NEWSLETTER</h4>
    <p>Register Your email address to get information ablout us</p>
    <div class="email-field">Email Address</div>
    <span class="subscribe">SUBSCRIBE</span>
  </div>

  <div class="abs f-col" style="left:901px;top:44px;width:220px">
    <h4>FOLLOW US</h4>
    <p>Lorem ipsum dolor sit amet, conse ctetur adipiscing elit. Nulla in purus nibh. Donec ornare</p>
    <div class="socials">
      <span aria-label="Social profile one"></span><span aria-label="Social profile two"></span><span aria-label="Social profile three"></span><span aria-label="Social profile four"></span><span aria-label="Social profile five"></span>
    </div>
  </div>

  <div class="abs footer-line"></div>
  <p class="abs copyright">© Copyright 2018 Brisendale Remodeling.All Rights Reserved</p>
</footer>

</body>
</html>
```